Poster for Sparkler-style Christmas music and dance show.

I need a poster for a Christmas music and dance show styled after the Harbor Lane Sparklers. Attached are samples of posters for previous years. I like the font style and colors of the blue one. The design should contain an ornament design with dancers dancing on it. The dancers should be cartoon style, not photo real. A sample is attached.
The poster MUST contain the VelMUSE logo, sponsor logos, the dates (December 12-13, 2015), the location (Lia & Peter Hollins Theatre, 4150 Brindle Crest, Lakeway, TX), VelMUSE contact info (www.vel-muse.org and 512-640-3187 ext 204), and "Directed and Choreographed by Wesley Hartman."
Logos are all attached. Finalized files needed in sizes: 12x18, 4x6, and 30x48 inches.

Target Market(s)

Community Theatre patrons

Industry/Entity Type

Radio

Font styles to use
Serif

Colors
0792cd
33a6d7
85cae6
ecf7fb
ffffff

Requirements
Must have
• VelMUSE logo (attached)
• sponsor logos: Nadia Poll Photography, Brimwell Dentistry, Topside Grill, Up Tempo (attached)
• Show dates: December 12-13, 2015)
• Show Location: Lia & Peter Hollins Theatre, 4150 Brindle Crest, Lakeway, TX)
• VelMUSE contact info: www.vel-muse.org and 512-640-3187 ext 204
• "Directed and Choreographed by Wesley Hartman"
• An ornament design with dancers on it. The dancers should be cartoon style, not photo real. A sample of a dancer graphic is attached.
Nice to have
• snowflakes or other winter themes

```html
<!DOCTYPE html>
<html lang="en">
<head>
<meta charset="utf-8">
<title>Holiday – VelMUSE Broadway Company</title>
<link href="https://fonts.googleapis.com/css2?family=Great+Vibes&family=Raleway:wght@300;500;700&display=swap" rel="stylesheet">
<style>
  :root {
    --blue-deep: #0792cd;
    --blue-mid: #33a6d7;
    --blue-soft: #85cae6;
    --blue-mist: #ecf7fb;
    --white: #ffffff;
    --ink: #2b3a46;
    --panel-dark: #0b4f6e;
    --panel-light: #2f9cc4;
  }
  * { margin: 0; padding: 0; box-sizing: border-box; }
  html, body { width: 800px; height: 1200px; overflow: hidden; background: var(--white); }
  .poster {
    position: relative; width: 800px; height: 1200px; background: var(--white);
    font-family: 'Raleway', sans-serif; color: var(--blue-deep); text-align: center;
  }
  .presenter { position: absolute; top: 18px; left: 0; right: 0; }
  .presenter-name {
    font-size: 50px; font-weight: 700; letter-spacing: 1px; color: var(--blue-deep); line-height: 1;
  }
  .presenter-line {
    margin-top: 6px; font-size: 13px; font-weight: 700; letter-spacing: 3px; color: var(--blue-deep);
  }
  .show-art {
    position: absolute; top: 118px; left: 54px; width: 692px; height: 680px;
    background:
      radial-gradient(ellipse at 50% 45%, var(--panel-light) 0%, var(--panel-dark) 70%, transparent 71%),
      radial-gradient(ellipse at 50% 50%, var(--blue-mist) 60%, var(--white) 80%);
    border-radius: 40px;
  }
  .show-title {
    position: absolute; top: 370px; left: 0; right: 0;
    font-size: 118px; font-weight: 300; letter-spacing: 6px; color: var(--white); line-height: 1;
  }
  .credits { position: absolute; top: 812px; left: 0; right: 0; }
  .label {
    font-family: 'Great Vibes', cursive; font-size: 28px; color: var(--blue-soft); line-height: 1;
  }
  .value { font-size: 27px; font-weight: 700; color: var(--blue-deep); line-height: 1.15; margin-bottom: 8px; }
  .value.venue { font-size: 23px; font-weight: 500; color: var(--ink); }
  .contact-bar {
    position: absolute; top: 1006px; left: 54px; width: 692px; height: 32px;
    background: var(--blue-mid); color: var(--white);
    font-size: 21px; font-weight: 500; line-height: 32px;
  }
  .sponsors-label { position: absolute; top: 1044px; left: 0; right: 0; }
  .sponsor-row {
    position: absolute; left: 60px; right: 60px;
    display: flex; justify-content: center; align-items: center; gap: 30px;
  }
  .sponsor-row.primary { top: 1086px; }
  .sponsor-row.local { top: 1142px; gap: 22px; }
  .sponsor { display: flex; align-items: center; gap: 7px; font-size: 14px; font-weight: 700; color: var(--ink); text-align: left; line-height: 1.1; }
  .sponsor .mark-circle { width: 26px; height: 26px; border-radius: 50%; background: var(--blue-deep); flex: none; }
  .sponsor .mark-square { width: 24px; height: 24px; background: var(--blue-soft); flex: none; }
  .divider { width: 1px; height: 36px; background: var(--ink); }
</style>
</head>
<body>
<main class="poster">
  <header class="presenter">
    <div class="presenter-name">VelMUSE</div>
    <div class="presenter-line">BROADWAY COMPANY PRESENTS</div>
  </header>

  <div class="show-art" role="img" aria-label="Blue wooden panel with frosted snowy edges, a red ribbon and bow across the top, falling snow, evergreen sprigs and white silhouettes of dancers in a kick line"></div>
  <h1 class="show-title">HOLIDAY</h1>

  <section class="credits">
    <p class="label">Directed and Choreographed by</p>
    <p class="value">WESLEY HARTMAN</p>
    <p class="label">Date</p>
    <p class="value">DECEMBER 12-13, 2015</p>
    <p class="label">Location</p>
    <p class="value venue">Lia &amp; Peter Hollins Theatre, 4150 Brindle Crest, Lakeway, TX)</p>
  </section>

  <div class="contact-bar">www.vel-muse.org | 512-640-3187 ext 204</div>

  <p class="label sponsors-label">Sponsors</p>
  <div class="sponsor-row primary">
    <div class="sponsor"><span class="mark-circle"></span>Lone Prairie<br>Arts Council</div>
    <div class="sponsor"><span class="mark-square"></span>CRAFT FORWARD</div>
    <span class="divider"></span>
    <div class="sponsor">Civic Fund<br>for the Arts</div>
  </div>
  <div class="sponsor-row local">
    <div class="sponsor"><span class="mark-square"></span>Topside<br>Grill</div>
    <div class="sponsor">Nadia Poll<br>Photography</div>
    <div class="sponsor"><span class="mark-circle"></span>The Laurel</div>
    <div class="sponsor">Up Tempo</div>
    <div class="sponsor"><span class="mark-square"></span>Brimwell<br>Dentistry</div>
  </div>
</main>
</body>
</html>
```